Logo Tweaks & Stationery Design Project for Energy Management Co

We are a specialist metering company trading for over 60 years and have recently developed GPRS metering infrastructure & monitoring services. For more information please see http://www.kestrel-vale.example/remote-meter-reading.html

Due to the success of this system it’s become necessary to open a new company “Brightwell Gauge Ltd” and this project is for relevant stationary designs for our documents.

I need something modern and clear to match our new logo style. Feel free to play around with the colors and tweak the logo if you like.

Maybe with some line chart animation on the header relating to our online services. ( See inspiration file )

Thanks
Derek

Target Market(s)

Renewable Energy Generation Monitoring, Energy Management, Remote Monitoring and Tennant Billing.

Industry/Entity Type

It Company

Requirements
Nice to have
• 100% Carbon neutral hosting
Should not have
• "Clip-Art" should not be used.

```html
<!DOCTYPE html>
<html lang="en">
<head>
<meta charset="utf-8">
<title>Brightwell Gauge Ltd – Stationery</title>
<link rel="stylesheet" href="https://fonts.googleapis.com/css2?family=Michroma&family=Tinos&display=swap">
<style>
  :root {
    --backdrop: #d2b48a;
    --brand-red: #bd1f2e;
    --brand-blue: #233a96;
    --name-blue: #2e2fa6;
    --footer-grey: #6d6d6f;
    --paper: #ffffff;
    --edge: #7a7a7a;
    --label: #1a1a1a;
  }
  * { margin: 0; padding: 0; box-sizing: border-box; }
  html, body { width: 1071px; height: 1200px; overflow: hidden; }
  body { background: var(--backdrop); position: relative; font-family: "Michroma", sans-serif; }

  .sheet, .envelope, .label { position: absolute; }

  /* Letterhead */
  .sheet { left: 142px; width: 353px; background: var(--paper); }
  .sheet--red { top: 48px; height: 496px; }
  .sheet--blue { top: 664px; height: 499px; }
  .sheet__header { position: absolute; left: 0; top: 0; width: 353px; height: 64px; }
  .sheet--red .sheet__header { background: var(--brand-red); }
  .sheet--blue .sheet__header { background: var(--brand-blue); }
  .sheet__name {
    position: absolute; left: 6px; top: 10px;
    font-size: 50px; line-height: 1; letter-spacing: -1px;
  }
  .sheet--red .sheet__name { color: var(--name-blue); }
  .sheet--blue .sheet__name { color: var(--brand-red); }

  .footer-strip {
    position: absolute; left: 0; bottom: 0; width: 100%;
    background: var(--footer-grey); color: var(--name-blue);
    font-size: 14px; letter-spacing: 4px; text-align: center;
    font-variant: small-caps; white-space: nowrap; overflow: hidden;
  }
  .sheet .footer-strip { height: 17px; line-height: 17px; }
  .envelope .footer-strip { height: 19px; line-height: 19px; }

  /* Envelopes */
  .envelope { width: 370px; }
  .envelope svg { display: block; }
  .envelope--back { left: 640px; top: 137px; }
  .envelope--front-blue { left: 661px; top: 458px; width: 367px; }
  .envelope--front-red { left: 661px; top: 763px; width: 367px; }
  .envelope__name {
    position: absolute; left: 12px; top: 152px;
    font-size: 50px; line-height: 1; color: var(--name-blue); letter-spacing: -1px;
  }

  /* Presentation labels */
  .label { font-family: "Tinos", serif; color: var(--label); }
  .label--small { font-size: 14px; }
  .label--large { font-size: 23px; }
</style>
</head>
<body>

  <!-- Letterhead, red header -->
  <section class="sheet sheet--red">
    <div class="sheet__header"></div>
    <div class="sheet__name">BG</div>
    <div class="footer-strip">BrightwellGauge</div>
  </section>
  <p class="label label--small" style="left:150px; top:578px;">Letter Head</p>

  <!-- Letterhead, blue header -->
  <section class="sheet sheet--blue">
    <div class="sheet__header"></div>
    <div class="sheet__name">BG</div>
    <div class="footer-strip">BrightwellGauge</div>
  </section>

  <!-- Envelope back -->
  <section class="envelope envelope--back">
    <svg width="370" height="238" viewBox="0 0 370 238" aria-hidden="true">
      <rect x="0.5" y="66" width="369" height="171" fill="var(--paper)" stroke="var(--edge)"/>
      <polyline points="1,67 172,104 369,67" fill="none" stroke="var(--edge)" stroke-width="1"/>
      <polygon points="0,67 14,22 192,0 356,22 370,67" fill="var(--brand-blue)"/>
    </svg>
    <div class="footer-strip">BrightwellGauge</div>
  </section>
  <p class="label label--large" style="left:651px; top:379px;">Back</p>
  <p class="label label--large" style="left:575px; top:436px;">Envelop</p>

  <!-- Envelope front, blue band -->
  <section class="envelope envelope--front-blue">
    <svg width="367" height="238" viewBox="0 0 367 238" aria-hidden="true">
      <polygon points="0.5,67 12,30 190,0.5 350,30 366.5,67" fill="var(--paper)" stroke="var(--edge)"/>
      <rect x="0.5" y="67" width="366" height="170.5" fill="var(--paper)" stroke="var(--edge)"/>
      <rect x="0" y="202" width="367" height="36" fill="var(--brand-blue)"/>
      <path d="M282 238 C282 170 320 146 367 144 L367 238 Z" fill="var(--brand-blue)"/>
      <path d="M290 238 C292 178 326 154 367 152 L367 238 Z" fill="var(--brand-red)"/>
    </svg>
    <div class="envelope__name">BG</div>
  </section>
  <p class="label label--large" style="left:662px; top:701px;">Front</p>
  <p class="label label--large" style="left:575px; top:739px;">Envelop</p>

  <!-- Envelope front, red band -->
  <section class="envelope envelope--front-red">
    <svg width="367" height="238" viewBox="0 0 367 238" aria-hidden="true">
      <polygon points="0.5,67 12,30 190,0.5 350,30 366.5,67" fill="var(--paper)" stroke="var(--edge)"/>
      <rect x="0.5" y="67" width="366" height="170.5" fill="var(--paper)" stroke="var(--edge)"/>
      <rect x="0" y="200" width="367" height="38" fill="var(--brand-red)"/>
      <path d="M282 238 C282 170 320 146 367 144 L367 238 Z" fill="var(--brand-red)"/>
      <path d="M290 238 C292 178 326 154 367 152 L367 238 Z" fill="var(--brand-blue)"/>
    </svg>
    <div class="envelope__name">BG</div>
  </section>
  <p class="label label--large" style="left:676px; top:1016px;">Front</p>

</body>
</html>
```